Oakmere Animal Care Group of Central Pennsylvania

I need a business card design for a new company in Harrisburg PA called "Animal Care Oakmere Group of Central PA". I will be providing relief services for veterinarians who need coverage during vacations; sick/maternity leave, etc. I would like to see the veterinarian symbol incorporated in the design in combination with animals (dogs /cats/birds/reptiles an pocket pets). Include My full name: Tomás R. Quintaval DVM, MLAS, BS. Also include my e mail (dvmtrq@mailbrook.net) and phone number 5552846017

Target Market(s)

Small Animal Veterinarian, practice owner

Industry/Entity Type

Business

Contact Information for Business Card

Oakmere Animal Care Group of Central PA

Font styles to use
Script

Requirements
Must have
• Veterinarian caduceus (see image) and Small animals (pets) within the logo.
Nice to have
• Give a sense of relaxation (vacationing)
Should not have
• Large animals, i.e. horses, cows, zoo animals...

```html
<!DOCTYPE html>
<html lang="en">
<head>
<meta charset="utf-8">
<title>Animal Care Oakmere Group of Central PA – Business Card</title>
<link rel="stylesheet" href="https://fonts.googleapis.com/css2?family=Cinzel:wght@700&family=Pinyon+Script&display=swap">
<style>
  :root {
    --backdrop: #1e1e1e;
    --card: #ffffff;
    --ink: #111111;
    --brand-red: #a3262a;
    --accent-red: #d42a2e;
  }
  * { margin: 0; padding: 0; box-sizing: border-box; }
  html, body { width: 1189px; height: 1200px; overflow: hidden; }
  body { background: var(--backdrop); position: relative; font-family: Arial, Helvetica, sans-serif; }

  .card {
    position: absolute;
    left: 140px;
    width: 917px;
    height: 521px;
    background: var(--card);
    border-radius: 26px;
  }
  .card--front { top: 46px; }
  .card--back { top: 623px; }

  .brand-mark {
    position: absolute;
    border: 10px solid var(--brand-red);
    border-radius: 50%;
  }
  .card--front .brand-mark { left: 359px; top: 130px; width: 212px; height: 212px; }
  .card--back .brand-mark { left: 151px; top: 150px; width: 164px; height: 164px; border-width: 8px; }

  .brand-name {
    position: absolute;
    font-family: "Cinzel", Georgia, serif;
    font-weight: 700;
    text-align: center;
    white-space: nowrap;
  }
  .brand-name__line { display: block; }
  .brand-name__line--main { color: var(--ink); }
  .brand-name__line--region { color: var(--accent-red); }

  .card--front .brand-name { left: 0; width: 930px; top: 344px; }
  .card--front .brand-name__line--main { font-size: 35px; line-height: 44px; }
  .card--front .brand-name__line--region { font-size: 28px; line-height: 36px; }

  .card--back .brand-name { left: 33px; width: 400px; top: 326px; }
  .card--back .brand-name__line--main { font-size: 26px; line-height: 32px; }
  .card--back .brand-name__line--region { font-size: 21px; line-height: 28px; }

  .divider {
    position: absolute;
    left: 456px; top: 91px;
    width: 2px; height: 343px;
    background: var(--brand-red);
  }

  .person { position: absolute; left: 497px; top: 116px; }
  .person__name {
    font-family: "Pinyon Script", cursive;
    font-size: 40px;
    color: var(--ink);
    line-height: 1.15;
    white-space: nowrap;
  }
  .person__credentials {
    font-size: 18px;
    color: var(--ink);
    margin-top: 0;
  }
  .person__title {
    font-size: 23px;
    color: var(--accent-red);
    margin-top: 4px;
  }

  .contact { position: absolute; left: 499px; top: 294px; list-style: none; }
  .contact__item {
    display: flex; align-items: center;
    font-size: 25px; color: var(--ink);
    height: 35px;
  }
  .contact__icon {
    width: 27px; height: 27px; margin-right: 10px;
    background: var(--brand-red); border-radius: 4px;
    display: flex; align-items: center; justify-content: center;
  }
</style>
</head>
<body>

<section class="card card--front">
  <div class="brand-mark" aria-hidden="true"></div>
  <h1 class="brand-name">
    <span class="brand-name__line brand-name__line--main">Animal Care Oakmere</span>
    <span class="brand-name__line brand-name__line--region">Group of Central PA</span>
  </h1>
</section>

<section class="card card--back">
  <div class="brand-mark" aria-hidden="true"></div>
  <p class="brand-name">
    <span class="brand-name__line brand-name__line--main">Animal Care Oakmere</span>
    <span class="brand-name__line brand-name__line--region">Group of Central PA</span>
  </p>

  <div class="divider" aria-hidden="true"></div>

  <div class="person">
    <p class="person__name">Tomás R. Quintaval</p>
    <p class="person__credentials">DVM, MLAS, BS</p>
    <p class="person__title">Managing Director</p>
  </div>

  <ul class="contact">
    <li class="contact__item">
      <span class="contact__icon">
        <svg width="19" height="19" viewBox="0 0 24 24" aria-hidden="true">
          <path fill="#fff" d="M6.6 10.8a15 15 0 0 0 6.6 6.6l2.2-2.2c.3-.3.7-.4 1-.2 1.1.4 2.3.6 3.6.6.6 0 1 .4 1 1V20c0 .6-.4 1-1 1A17 17 0 0 1 3 4c0-.6.4-1 1-1h3.5c.6 0 1 .4 1 1 0 1.3.2 2.5.6 3.6.1.3 0 .7-.2 1z"/>
        </svg>
      </span>
      5552846017
    </li>
    <li class="contact__item">
      <span class="contact__icon">
        <svg width="19" height="15" viewBox="0 0 24 18" aria-hidden="true">
          <rect x="1" y="1" width="22" height="16" fill="none" stroke="#fff" stroke-width="2"/>
          <path d="M1 1l11 9 11-9M1 17l8-7M23 17l-8-7" fill="none" stroke="#fff" stroke-width="2"/>
        </svg>
      </span>
      dvmtrq@mailbrook.net
    </li>
  </ul>
</section>

</body>
</html>
```